Crestline Staffing PEO - Web Build for Professional Employment Organization

We need a website built for our new PEO (professional employment organization). This company will offer third party Human Resource services to companies who are looking to outsource:<br/>Recruiting<br/>Administrative Onboarding<br/>New hire training, ongoing training and development<br/>Payroll/compensation processing/services<br/>Employee Relations<br/>Unemployment Claim Facilitation<br/>Benefits Plans and Administration<br/><br/>I have attached the logo below. Please use that as a reference and color match as best as possible. <br/><br/>Here are some of the competitor's websites:<br/>https://www.velmorahr.com/ <br/>https://www.trundelpay.com/<br/>https://www.trundelpay.com/<br/>https://www.qzn.com/<br/>https://www.bremwickhr.com/<br/>https://orvalepeo.com/contact-orvale/<br/><br/>

Target Market(s)

Startups and mid-sized businesses

Number of Pages Required

5+ page

Font styles to use
Sans Serif

Colors
0592cd

Requirements
Must have
• Features Pages
• SEO driven keyword rich content
• Strong focus on our ability to provide unemployment claim facilitation services as well as mandatory training/certification fulfillment
Nice to have
• I'd like to see one mockup with a Live Chat version if possible. In theory, the Live Chat messages would go directly to our front desk person.

```html
<!DOCTYPE html>
<html lang="en">
<head>
<meta charset="utf-8">
<title>Crestline Staffing PEO</title>
<link href="https://fonts.googleapis.com/css2?family=Roboto:ital,wght@0,300;0,400;0,500;0,700;1,400&display=swap" rel="stylesheet">
<style>
:root{
  --blue:#1b8fd0;
  --blue-dark:#1579c2;
  --ink:#333d4f;
  --text:#6b7280;
  --navy:#2e3a52;
  --footer:#2f3b54;
  --line:#d5dbe3;
  --white:#ffffff;
}
*{margin:0;padding:0;box-sizing:border-box}
html,body{width:1200px;height:4249px;overflow:hidden}
body{font-family:'Roboto',sans-serif;color:var(--ink);background:var(--white);position:relative}
.abs{position:absolute}
section,header,footer,.topbar{position:absolute;left:0;width:1200px}

.topbar{top:0;height:40px;background:#f4f6f9}
.topbar a{position:absolute;top:13px;font-size:11px;color:#444;text-decoration:none;letter-spacing:.2px}

.site-header{top:40px;height:100px;background:var(--white)}
.brand{position:absolute;left:147px;top:34px;display:flex;align-items:center;gap:10px}
.brand-dot{width:18px;height:18px;border-radius:50%;background:var(--blue)}
.brand-name{font-size:22px;font-weight:700;color:var(--blue);letter-spacing:.3px}
.main-nav a{position:absolute;top:47px;font-size:14px;font-weight:500;color:var(--ink);text-decoration:none}
.main-nav a.active{color:var(--blue)}
.main-nav .sep{position:absolute;top:46px;width:1px;height:16px;background:#bbb}

.hero{top:140px;height:598px;background:linear-gradient(100deg,#c9d7e4 0%,#dfe7ef 35%,#e9eef3 55%,#bfc9d3 75%,#9aa7b5 100%)}
.hero-circle{position:absolute;left:116px;top:83px;width:406px;height:406px;border-radius:50%;background:rgba(27,143,208,.92);text-align:center;color:#fff}
.hero-circle h1{margin-top:130px;font-size:30px;font-weight:500;line-height:36px;text-transform:uppercase}
.hero-circle .btn-outline{display:inline-block;margin-top:22px;width:170px;height:48px;line-height:46px;border:2px solid #fff;color:#fff;font-size:15px;font-weight:500;text-decoration:none}
.hero .arrow{position:absolute;top:253px}

.services{top:738px;height:943px;background:var(--white)}
.section-title{position:absolute;left:0;width:1200px;text-align:center;font-weight:700;text-transform:uppercase}
.services .section-title{top:78px;font-size:32px;color:var(--blue)}
.services .lead{position:absolute;left:250px;top:132px;width:680px;text-align:center;font-size:15px;line-height:23px;color:var(--text)}
.service{position:absolute;width:270px}
.service h3{font-size:20px;font-weight:500;line-height:26px;color:var(--ink);margin-top:18px}
.service p{font-size:14.5px;line-height:26px;color:var(--text);margin-top:14px}
.btn-line{position:absolute;border:2px solid var(--blue);color:var(--ink);font-size:15px;font-weight:500;text-align:center;text-decoration:none;background:#fff}

.testimonial{top:1681px;height:523px;background:var(--navy)}
.testimonial-photo{position:absolute;left:495px;top:0;width:705px;height:523px;background:linear-gradient(90deg,#2e3a52 0%,#6a5a58 25%,#a58a78 45%,#8b8c90 70%,#5d6673 100%)}
.testimonial h2{position:absolute;left:139px;top:118px;font-size:27px;font-weight:700;color:#fff}
.testimonial blockquote{position:absolute;left:139px;top:170px;width:400px;font-size:15px;font-style:italic;line-height:27px;color:#fff}
.testimonial .author{position:absolute;left:139px;top:310px;font-size:15px;font-weight:700;color:#fff}
.testimonial .company{position:absolute;left:139px;top:333px;font-size:14px;color:#fff}
.thumb{position:absolute;top:2121px;width:221px;height:128px}

.courses{top:2249px;height:615px;background:var(--white)}
.courses .section-title{top:86px;font-size:26px;font-weight:500;color:var(--ink)}
.course-img{position:absolute;width:296px;height:216px}
.course-card{position:absolute;width:261px;height:142px;background:#fff;box-shadow:0 2px 8px rgba(0,0,0,.12);text-align:center;padding-top:28px}
.course-card h3{font-size:17px;font-weight:500;line-height:19px;color:var(--ink)}
.course-card p{font-size:11px;line-height:18px;color:var(--text);margin:12px 22px 0}
.course-card.dark{background:var(--navy)}
.course-card.dark h3,.course-card.dark p{color:#fff}

.get-started{top:2864px;height:499px;background:linear-gradient(90deg,#1ea2d9 0%,#1b8fd0 50%,#1579c2 100%);color:#fff}
.get-started .section-title{top:62px;font-size:28px;color:#fff}
.get-started .lead{position:absolute;left:270px;top:111px;width:660px;text-align:center;font-size:13px;line-height:20px}
.step{position:absolute;width:230px;text-align:center;top:215px}
.step h3{font-size:17px;font-weight:700;margin-top:24px;text-transform:uppercase}
.step p{font-size:13px;line-height:20px;margin-top:12px;color:#d6ecf8}

.contact{top:3363px;height:497px;background:linear-gradient(90deg,#e3e9f1 0%,#eef2f7 40%,#e5ebf2 70%,#d5dde8 100%)}
.contact .section-title{top:54px;font-size:26px;font-weight:500;color:var(--ink)}
.field{position:absolute;background:#fff;font-size:14px;color:#444;padding:16px 20px}

.site-footer{top:3860px;height:389px;background:var(--footer);color:#fff}
.foot-col{position:absolute;top:66px}
.foot-col h4{font-size:15px;font-weight:500;margin-bottom:12px}
.foot-col a{display:block;font-size:12.5px;color:#c3c9d4;text-decoration:none;line-height:25px}
.foot-col a svg{vertical-align:-2px;margin-right:8px}
.live-chat{position:absolute;left:677px;top:218px;width:155px;height:38px;background:var(--blue);display:flex;align-items:center;color:#fff;font-size:12.5px;font-weight:500}
.live-chat .chat-icon{width:46px;height:38px;background:#fff;display:flex;align-items:center;justify-content:center;margin-right:10px}
.foot-rule{position:absolute;left:147px;top:314px;width:883px;height:1px;background:#56617a}
.legal{position:absolute;top:337px;font-size:12.5px;color:#c3c9d4}
.legal-links{position:absolute;left:806px;top:337px;font-size:12.5px;color:#c3c9d4}
</style>
</head>
<body>

<div class="topbar">
  <a style="left:723px" href="#">LOGIN</a>
  <a style="left:780px" href="#">INTEGRATIONS</a>
  <a style="left:888px" href="#">SUPPORT</a>
  <a style="left:965px" href="#">RESOURCES</a>
</div>

<header class="site-header">
  <div class="brand"><span class="brand-dot"></span><span class="brand-name">Crestline Staffing PEO</span></div>
  <nav class="main-nav">
    <a class="active" style="left:432px" href="#">ABOUT US</a><span class="sep" style="left:519px"></span>
    <a style="left:538px" href="#">SERVICES</a><span class="sep" style="left:620px"></span>
    <a style="left:641px" href="#">SOLUTION</a><span class="sep" style="left:727px"></span>
    <a style="left:748px" href="#">TESTIMONIAL</a><span class="sep" style="left:858px"></span>
    <a style="left:877px" href="#">COURSES</a><span class="sep" style="left:960px"></span>
    <a style="left:979px" href="#">CONTACT</a>
  </nav>
</header>

<section class="hero" role="img" aria-label="Photo of a woman in glasses working on a laptop in a bright office">
  <div class="hero-circle">
    <h1>We provide payroll<br>compensation<br>processing</h1>
    <a class="btn-outline" href="#">LEARN MORE</a>
  </div>
  <svg class="arrow" style="left:38px" width="24" height="40" viewBox="0 0 24 40"><path d="M20 4 L5 20 L20 36" fill="none" stroke="#fff" stroke-width="4"/></svg>
  <svg class="arrow" style="left:1140px" width="24" height="40" viewBox="0 0 24 40"><path d="M4 4 L19 20 L4 36" fill="none" stroke="#fff" stroke-width="4"/></svg>
</section>

<section class="services">
  <h2 class="section-title">Our Services</h2>
  <p class="lead">Fusce tellus Sed metus augue convallis et vehicula ut pulvinar eu ante Integer orci tellus tristique vitae consequat nec porta vel lectus Nulla sit amet dui lectus cursus eu</p>

  <div class="service" style="left:182px;top:277px">
  <svg width="60" height="60" viewBox="0 0 60 60" fill="none" stroke="#1b8fd0" stroke-width="2"><circle cx="24" cy="24" r="16"/><circle cx="24" cy="20" r="5"/><path d="M15 33 q9-10 18 0"/><path d="M36 36 L52 52"/></svg>
  <h3>Recruiting</h3>
  <p>Fusce tellus Sed metus augue convallis et vehicula ut pulvinar eu ante Integer orci tellus tri</p></div>

  <div class="service" style="left:484px;top:277px">
  <svg width="60" height="60" viewBox="0 0 60 60" fill="none" stroke="#1b8fd0" stroke-width="2"><circle cx="30" cy="18" r="10"/><path d="M10 56 v-12 q0-10 20-10 q20 0 20 10 v12"/><path d="M30 34 v16"/></svg>
  <h3 style="margin-top:22px">Administrative<br>Onboarding</h3>
  <p>Fusce tellus Sed metus augue convallis et vehicula ut pulvi</p></div>

  <div class="service" style="left:791px;top:277px">
  <svg width="60" height="60" viewBox="0 0 60 60" fill="none" stroke="#1b8fd0" stroke-width="2"><rect x="16" y="4" width="40" height="28"/><path d="M22 26 l8-8 6 5 12-12"/><circle cx="10" cy="30" r="5"/><path d="M3 56 v-14 h14 v14"/><circle cx="30" cy="44" r="4"/><circle cx="46" cy="44" r="4"/><path d="M24 56 q6-8 12 0 M40 56 q6-8 12 0"/></svg>
  <h3>New hire training, ongoing training and development</h3>
  <p>Fusce tellus Sed metus augue convallis et vehicula ut</p></div>

  <div class="service" style="left:178px;top:550px">
  <svg width="62" height="62" viewBox="0 0 62 62" fill="none" stroke="#1b8fd0" stroke-width="2"><rect x="8" y="4" width="50" height="34" rx="3"/><path d="M8 14 h50 M16 24 h34"/><circle cx="18" cy="46" r="12" fill="#fff"/><text x="13" y="51" font-size="14" fill="#1b8fd0" stroke="none" font-family="Roboto,sans-serif">$</text></svg>
  <h3>Payroll/compensation processing/services</h3>
  <p>Fusce tellus Sed metus augue convallis et vehicula ut pu</p></div>

  <div class="service" style="left:479px;top:550px">
  <svg width="64" height="64" viewBox="0 0 64 64" fill="none" stroke="#1b8fd0" stroke-width="2"><circle cx="16" cy="14" r="8"/><path d="M4 34 q12-14 24 0"/><circle cx="46" cy="40" r="8"/><path d="M34 62 q12-14 24 0"/><path d="M36 8 h16 v10 M52 18 l-4-4 M28 46 h-16 v-10 M12 36 l4 4"/></svg>
  <h3>Employee<br>Relations</h3>
  <p>Fusce tellus Sed metus augue convallis et vehicula ut pulvin</p></div>

  <div class="service" style="left:786px;top:550px">
  <svg width="62" height="62" viewBox="0 0 62 62" fill="none" stroke="#1b8fd0" stroke-width="2"><path d="M8 4 h36 v54 h-36 z"/><rect x="14" y="12" width="10" height="10"/><path d="M30 14 h8 M14 30 h24 M14 38 h24 M14 46 h16"/><text x="44" y="22" font-size="16" fill="#1b8fd0" stroke="none" font-family="Roboto,sans-serif">$</text></svg>
  <h3>Unemployment<br>Claim Facilitation</h3>
  <p>Fusce tellus Sed metus augue convallis et vehicula</p></div>

  <a class="btn-line" href="#" style="left:499px;top:825px;width:216px;height:53px;line-height:49px">VIEW ALL SERVICES</a>
</section>

<section class="testimonial">
  <div class="testimonial-photo" role="img" aria-label="Photo of a smiling woman in glasses at a shared office desk with colleagues behind"></div>
  <h2>WHAT PEOPLE SAYS</h2>
  <blockquote>Fusce tellus Sed metus augue convallis et vehicula ut pulvinar eu ante Integer orci tellus tristique vitae consequat nec porta vel lectus Nulla sit amet diam aliquam enim Proin dui lectus cursus eu</blockquote>
  <div class="author">By Author Name</div>
  <div class="company">Company Name</div>
  <svg class="abs" style="left:771px;top:186px" width="80" height="80" viewBox="0 0 80 80"><circle cx="40" cy="40" r="36" fill="none" stroke="#fff" stroke-width="5"/><path d="M32 24 L56 40 L32 56 Z" fill="#fff"/></svg>
</section>
<div class="thumb" style="left:134px;background:linear-gradient(135deg,#7a3a30,#c9b3a5);border-top:4px solid var(--blue)" role="img" aria-label="Thumbnail photo of a smiling woman in an office"></div>
<svg class="abs" style="left:234px;top:2110px" width="22" height="12" viewBox="0 0 22 12"><path d="M0 12 L11 0 L22 12 Z" fill="#1b8fd0"/></svg>
<div class="thumb" style="left:373px;background:linear-gradient(135deg,#b9c2cc,#4a4f58)" role="img" aria-label="Thumbnail photo of a man in a suit at a desk"></div>
<div class="thumb" style="left:611px;background:linear-gradient(135deg,#9aa6b6,#d5dbe3)" role="img" aria-label="Thumbnail photo of colleagues working on laptops"></div>
<div class="thumb" style="left:850px;background:linear-gradient(135deg,#c8c2ba,#8b6f5e)" role="img" aria-label="Thumbnail photo of a smiling woman"></div>

<section class="courses">
  <h2 class="section-title">Training Certification Courses</h2>
  <div class="course-img" style="left:154px;top:150px;background:linear-gradient(135deg,#9fb3c6,#3f5670)" role="img" aria-label="Photo of a man in glasses working at a computer"></div>
  <div class="course-card" style="left:172px;top:330px"><h3>Fusce tellus Sed metus<br>augue convallis</h3><p>Curabitur vel dolor ultrices ipsum dictum tristique Praesent vitae lacus Ut</p></div>
  <div class="course-img" style="left:470px;top:154px;background:linear-gradient(135deg,#2f3f7a,#b8b0c0)" role="img" aria-label="Photo of a woman in glasses writing at a desk"></div>
  <div class="course-card dark" style="left:489px;top:334px"><h3>Fusce tellus Sed metus<br>augue convallis</h3><p>Curabitur vel dolor ultrices ipsum dictum tristique Praesent vitae lacus Ut</p></div>
  <div class="course-img" style="left:787px;top:157px;background:linear-gradient(135deg,#dfe4ea,#8a97a8)" role="img" aria-label="Photo of a smiling man in glasses at a laptop"></div>
  <div class="course-card" style="left:806px;top:338px"><h3>Fusce tellus Sed metus<br>augue convallis</h3><p>Curabitur vel dolor ultrices ipsum dictum tristique Praesent vitae lacus Ut</p></div>
  <a class="btn-line" href="#" style="left:490px;top:516px;width:255px;height:55px;line-height:51px">VIEW MORE COURSES</a>
</section>

<section class="get-started">
  <h2 class="section-title">Get Started Today</h2>
  <p class="lead">Augiat in pede Fusce tellus Sed metus augue convallis et vehicula ut pulvinar eu ante Integer orci tellus tristique vitae consequat nec mauris viverra in gravida eu mattis in ante Morbi</p>

  <div class="step" style="left:188px">
    <svg width="64" height="64" viewBox="0 0 64 64" fill="none" stroke="#fff" stroke-width="2"><circle cx="32" cy="32" r="9"/><circle cx="32" cy="8" r="6"/><circle cx="32" cy="56" r="6"/><circle cx="10" cy="20" r="6"/><circle cx="54" cy="20" r="6"/><circle cx="10" cy="44" r="6"/><circle cx="54" cy="44" r="6"/><path d="M32 14v9M32 41v9M15 23l9 5M49 23l-9 5M15 41l9-5M49 41l-9-5"/></svg>
    <h3>Get Connect</h3>
    <p>At vehicula ut pulvinar eu ante Integer orci tellus tristique vitae consequat nec mauris</p>
  </div>
  <svg class="abs" style="left:406px;top:240px" width="40" height="20" viewBox="0 0 40 20" fill="none" stroke="#cfe6f5" stroke-width="2"><path d="M0 10h36M28 2l8 8-8 8"/></svg>
  <div class="step" style="left:484px">
    <svg width="64" height="64" viewBox="0 0 64 64" fill="none" stroke="#fff" stroke-width="2"><rect x="20" y="4" width="24" height="14" rx="3"/><circle cx="12" cy="26" r="6"/><circle cx="32" cy="26" r="6"/><circle cx="52" cy="26" r="6"/><path d="M4 60v-20h16v20M24 60v-20h16v20M44 60v-20h16v20"/></svg>
    <h3>Meet</h3>
    <p>At vehicula ut pulvinar eu ante Integer orci tellus tristique vitae consequat nec mauris</p>
  </div>
  <svg class="abs" style="left:759px;top:240px" width="40" height="20" viewBox="0 0 40 20" fill="none" stroke="#cfe6f5" stroke-width="2"><path d="M0 10h36M28 2l8 8-8 8"/></svg>
  <div class="step" style="left:790px">
    <svg width="64" height="64" viewBox="0 0 64 64" fill="none" stroke="#fff" stroke-width="2"><path d="M58 6 q-24 2-36 26 l10 10 q24-12 26-36z"/><circle cx="42" cy="22" r="5"/><path d="M22 32 h-12 l8-10 h12 M32 42 v12 l10-8 v-12 M16 48 l-10 10 M20 52 l-6 6 M12 44 l-6 6"/></svg>
    <h3>Elevate</h3>
    <p>At vehicula ut pulvinar eu ante Integer orci tellus tristique vitae consequat nec mauris</p>
  </div>
</section>

<section class="contact" role="img" aria-label="Faded photo of an office team in a meeting">
  <h2 class="section-title">Contact Crestline Staffing PEO</h2>
  <div class="field" style="left:248px;top:121px;width:345px;height:51px">First Name</div>
  <div class="field" style="left:611px;top:121px;width:342px;height:51px">Last Name</div>
  <div class="field" style="left:248px;top:183px;width:345px;height:52px">Email address</div>
  <div class="field" style="left:611px;top:183px;width:342px;height:52px">Phone Number</div>
  <div class="field" style="left:248px;top:246px;width:705px;height:112px">Message</div>
  <a class="btn-line" href="#" style="left:499px;top:378px;width:208px;height:55px;line-height:51px;color:var(--blue);font-size:17px">SUBMIT NOW</a>
</section>

<footer class="site-footer">
  <div class="foot-col" style="left:147px"><h4>QUICK LINKS</h4><a href="#">About Us</a><a href="#">Why Us</a><a href="#">What We Do</a><a href="#">Career</a><a href="#">Our Services</a></div>
  <div class="foot-col" style="left:317px"><h4>WHO WE SERVE</h4><a href="#">Business Size</a><a href="#">Industry</a><a href="#">Partners</a></div>
  <div class="foot-col" style="left:492px"><h4>RESOURCES</h4><a href="#">Demos</a><a href="#">What Others Say</a><a href="#">Articles and Insights</a><a href="#">Tools</a><a href="#">Contact Us</a><a href="#">Sitemap</a></div>
  <div class="foot-col" style="left:682px"><h4>CONTACT US</h4><a href="#">418 Harlow Street #B</a><a href="#">Texas 75021 TX</a><a href="#">(555) 014 2870</a><a href="#">info@crestlinestaffing.com</a></div>
  <div class="foot-col" style="left:921px"><h4>FOLLOW US</h4>
    <a href="#"><svg width="10" height="10"><rect width="10" height="10" fill="#c3c9d4"/></svg>Social Feed</a>
    <a href="#"><svg width="10" height="10"><rect width="10" height="10" fill="#c3c9d4"/></svg>Updates</a>
    <a href="#"><svg width="10" height="10"><rect width="10" height="10" fill="#c3c9d4"/></svg>Network</a>
    <a href="#"><svg width="10" height="10"><rect width="10" height="10" fill="#c3c9d4"/></svg>Gallery</a>
  </div>
  <div class="live-chat"><span class="chat-icon"><svg width="22" height="18" viewBox="0 0 22 18" fill="none" stroke="#1b8fd0" stroke-width="2"><path d="M2 2h18v10h-10l-5 4v-4h-3z"/></svg></span>LIVE CHAT<svg style="margin-left:14px" width="8" height="12" viewBox="0 0 8 12" fill="none" stroke="#fff" stroke-width="2"><path d="M2 1l5 5-5 5"/></svg></div>
  <div class="foot-rule"></div>
  <div class="legal" style="left:147px">© 2020 Company Name | All Rights Reserved | Disclaimer</div>
  <div class="legal-links">Privacy &nbsp;|&nbsp; Legal &nbsp;|&nbsp; Sitemap</div>
</footer>

</body>
</html>
```